Powerpoint design template for LUMOTEX for new digital platform

We would like to use a PowerPoint template, we would like to create a new page, we would like to create a new digital platform LUMOTEX for schools and parents for the creation of playful communication and educational tools for children to enhance their positive development, amaze them learn in a playful way. This platform is going to be the most creative, stimulating and innovative classroom, easy to use and fast to implement. Scrapbooking, collages ... Magazine, newsletters Diplomla / awards Slideshows Facebook Calendars Organizers Greetings Games ... This powerpoint template will be used essential to We are looking for a professional design, positioning our brand in the children market with an adult hearing. so you will need to find a good deal. Primary target: nurseries & schools from 0 to 18 years old and universities (in 2nd phase) Secondary target: small & medium businesses Third target: general public, and TPE If it is a color scheme, then it is suggested that it be marketed in Europe (UK, Italy, Spain) and in a 2nd Stage USA and other countries. multiple options for front page, insidious pages (multiple styles with limited text and extended text) and final contact page We need something to read, we can not do it too much, but we can not do it. , and inside pages aligned to our logo

Target Market(s)

Target 1; Education with teacher Target 2; parents and grandparents

Industry/Entity Type

Education

Font styles to use
Other font styles liked:
• not decided. but not too fancy

Requirements
Must have
• Multi page options for front page, page insides (multiple styles with limited text and extended text) and final page contact
Nice to have
• do not have a lot of ideas. We need something to read, we can not get away from it
Should not have
• not too fancy and busy: keep clarity & simplicity while reassuring on quality

```html
<!DOCTYPE html>
<html lang="en">
<head>
<meta charset="UTF-8">
<title>Lumotex – Project Slide</title>
<link href="https://fonts.googleapis.com/css2?family=Roboto+Condensed:wght@400;700&display=swap" rel="stylesheet">
<style>
  :root {
    --lime: #d9e043;
    --leaf: #8cc63f;
    --orange: #f7941d;
    --blue: #1bb0e6;
    --pink: #e8318a;
    --ink: #262626;
    --body: #7a7a7a;
    --paper: #ffffff;
  }
  * { margin: 0; padding: 0; box-sizing: border-box; }
  html, body { width: 1200px; height: 900px; overflow: hidden; background: var(--paper); }
  body { font-family: "Roboto Condensed", Arial, sans-serif; }
  .slide { position: relative; width: 1200px; height: 900px; overflow: hidden; background: var(--paper); }

  .header-band, .footer-band { position: absolute; left: 0; display: block; }
  .header-band { top: 0; width: 1200px; height: 120px; }
  .footer-band { bottom: 0; width: 1200px; height: 66px; }

  .slide-title {
    position: absolute; left: 30px; top: 28px;
    font-size: 46px; font-weight: 700; color: var(--ink); letter-spacing: 0.3px;
  }

  .brand {
    position: absolute; left: 995px; top: 36px; width: 190px;
    display: flex; flex-direction: column; align-items: flex-start;
  }
  .brand-row { display: flex; align-items: center; gap: 8px; }
  .brand-mark { width: 14px; height: 14px; background: var(--pink); }
  .brand-name { font-size: 36px; font-weight: 700; color: var(--ink); line-height: 1; }
  .brand-tagline { margin-top: 6px; font-size: 11px; font-weight: 700; color: var(--ink); letter-spacing: 1.5px; line-height: 1.2; }

  .sections { position: absolute; left: 30px; top: 168px; width: 1110px; }
  .section { position: relative; height: 196px; padding-left: 80px; }
  .section-art {
    position: absolute; left: 0; top: 0; width: 66px; height: 86px;
    border-radius: 10px; opacity: 0.85;
  }
  .section--blue .section-art { background: linear-gradient(160deg, #8fd6f2, var(--blue)); }
  .section--pink .section-art { background: linear-gradient(160deg, #f49ac4, var(--pink)); }
  .section--orange .section-art { background: linear-gradient(160deg, #fbc487, var(--orange)); }
  .section-heading { font-size: 31px; font-weight: 700; line-height: 1; padding-top: 16px; }
  .section--blue .section-heading { color: var(--blue); }
  .section--pink .section-heading { color: var(--pink); }
  .section--orange .section-heading { color: var(--orange); }
  .section-text { margin-top: 12px; font-size: 22.5px; line-height: 36px; color: var(--body); }

  .footer-url { position: absolute; left: 21px; bottom: 20px; font-size: 23px; color: var(--ink); }
  .footer-page { position: absolute; left: 1078px; bottom: 20px; font-size: 22px; color: var(--ink); }
</style>
</head>
<body>
<main class="slide">
  <svg class="header-band" viewBox="0 0 1200 120" aria-hidden="true">
    <polygon points="0,0 958,0 900,110 0,110" fill="var(--lime)"/>
    <polygon points="925,0 972,0 930,100 902,110" fill="var(--leaf)"/>
    <polygon points="948,0 985,0 945,70" fill="var(--lime)"/>
  </svg>

  <h1 class="slide-title">PROJECT TITLE HERE</h1>

  <div class="brand">
    <div class="brand-row">
      <span class="brand-mark"></span>
      <span class="brand-name">LUMOTEX</span>
    </div>
    <span class="brand-tagline">YOUR TAGLINE<br>GOES HERE</span>
  </div>

  <div class="sections">
    <section class="section section--blue">
      <div class="section-art" role="img" aria-label="Blue star wand illustration"></div>
      <h2 class="section-heading">SUBTEXT HERE</h2>
      <p class="section-text">Toffee caramels candy canes bonbon bonbon soufflé bonbon wafer. Topping I love halvah I love. Jujubes<br>lemon drops I love jelly pie chocolate bar. Biscuit oat cake carrot cake. Muffin jelly beans chocolate choco-<br>late. Sugar plum I love cheesecake marshmallow oreo cake sweet cookies topping jelly gummies.</p>
    </section>
    <section class="section section--pink">
      <div class="section-art" role="img" aria-label="Pink star wand illustration"></div>
      <h2 class="section-heading">SUBTEXT HERE</h2>
      <p class="section-text">Toffee caramels candy canes bonbon bonbon soufflé bonbon wafer. Topping I love halvah I love. Jujubes<br>lemon drops I love jelly pie chocolate bar. Biscuit oat cake carrot cake. Muffin jelly beans chocolate choco-<br>late. Sugar plum I love cheesecake marshmallow oreo cake sweet cookies topping jelly gummies.</p>
    </section>
    <section class="section section--orange">
      <div class="section-art" role="img" aria-label="Orange star wand illustration"></div>
      <h2 class="section-heading">SUBTEXT HERE</h2>
      <p class="section-text">Toffee caramels candy canes bonbon bonbon soufflé bonbon wafer. Topping I love halvah I love. Jujubes<br>lemon drops I love jelly pie chocolate bar. Biscuit oat cake carrot cake. Muffin jelly beans chocolate choco-<br>late. Sugar plum I love cheesecake marshmallow oreo cake sweet cookies topping jelly gummies.</p>
    </section>
  </div>

  <svg class="footer-band" viewBox="0 0 1200 66" aria-hidden="true">
    <polygon points="0,0 975,0 1035,66 0,66" fill="var(--lime)"/>
    <polygon points="975,0 1000,0 1060,66 1035,66" fill="var(--leaf)"/>
    <polygon points="998,0 1200,0 1200,66 1065,66" fill="var(--orange)"/>
  </svg>
  <span class="footer-url">www.lumotex.com</span>
  <span class="footer-page">Page : 01</span>
</main>
</body>
</html>
```